PostCard Design Project

I am making a mailing postcard
I am having the mailing printed using 4 color foil on certain parts.
I am looking for a design that maximizes the foil process where certain parts are done in foil to grab the customers attention (example: if there is a car on the postcard the headlights would be done in foil) .
I am targeting some industries, (auto, real estate, medical, beauty) I would like the post card to have examples of postcard ideas for 2 or 3 of these industries.
specs:
the postcard should be atleast 6.5x9 up to 8.5x11, I don't want to restrict the space for the creative as I don't want everything to look like a huge mess. both sides will be used.
the piece is a direct mail piece so it has to meet requirements of https://www.mailvantor.com/business/pdf/quick-reference-guide.pdf
text will be
"business with no limits, meet mailing with no addresses, gain new customers through "Open Porch Route Drop" reach new customers at their home without needing their address. "
I also want some current print specials I am running included.
-double your order FREE (order 500 business cards and get 1000)
-250 100lb gloss stock brochures 99.00
-business packages (cards, envelopes and letterhead) 299
-1000 flyers 140.40
-5000 postcards 179.99
A list of services
banners
booklets
brochures
business cards
calendars
catalogs
CD/DVD packages
envelopes
event tickets
flyers
hangtags
postcards
posters
presentation folders
rack cards
labels
table tents
window cling and decal
"order 24/7 orders@inkwillow.com" must be included
my logo is InkWillow will be supplied later
ive received some great designs. however Im looking for something a little more modern like some zorvel would put out. if the amount of words is too much please feel free to edit. also an idea i had for the list of services i offer is to have it transparent yet readable as the background of the postcard some small some big but covering the entire backgroud. you can then design on top of that with other thing. just an early morning thought
Reason: I have uploaded a sketch of my idea, please take time to look at it for an accurate depiction of what im looking for. feel free to add elements that make it pop off the page
Reason: We are getting close i will be providing feed back today

```html
<!DOCTYPE html>
<html lang="en">
<head>
<meta charset="utf-8">
<title>InkWillow Mailing Postcard</title>
<link rel="stylesheet" href="https://fonts.googleapis.com/css2?family=Open+Sans:wght@400;600;700;800&display=swap">
<style>
  :root {
    --page: #e9e6e1;
    --navy: #1b2c3d;
    --navy-deep: #0f1b28;
    --navy-light: #2a4057;
    --ink: #060708;
    --lime: #a8cf2f;
    --sky: #27b4e0;
    --photo-blue: #2bb0dc;
    --white: #ffffff;
    --grey-word: #55595e;
    --body-dark: #101214;
  }
  * { box-sizing: border-box; margin: 0; padding: 0; }
  html, body { width: 1200px; height: 900px; overflow: hidden; }
  body {
    background: var(--page);
    font-family: "Open Sans", sans-serif;
    display: flex;
    align-items: center;
    justify-content: center;
    gap: 40px;
  }
  .postcard {
    position: relative;
    width: 560px;
    height: 375px;
    overflow: hidden;
    box-shadow: 0 6px 18px rgba(0,0,0,.25);
  }
  .postcard__art { position: absolute; inset: 0; }

  /* Front */
  .front { background: var(--navy); }
  .front__logo {
    position: absolute; left: 28px; top: 26px;
    color: var(--white); font-weight: 800; font-size: 30px; line-height: 1.02;
    letter-spacing: .5px; text-align: center;
  }
  .front__specials {
    position: absolute; left: 262px; top: 20px; width: 290px;
    list-style: none; color: var(--body-dark); font-size: 11.5px; line-height: 1.35;
  }
  .front__specials li { padding-left: 14px; position: relative; }
  .front__specials li::before {
    content: ""; position: absolute; left: 2px; top: 6px;
    width: 5px; height: 5px; border-radius: 50%; background: var(--body-dark);
  }
  .front__message {
    position: absolute; left: 228px; top: 178px; width: 320px;
    color: var(--lime); font-size: 14px; line-height: 1.3;
  }
  .front__contact {
    position: absolute; left: 250px; top: 300px;
    color: #c9ccd0; font-size: 12.5px;
  }

  /* Back */
  .back { background: var(--ink); }
  .service-cloud {
    position: absolute; left: -60px; top: 4px; width: 720px;
    font-size: 15px; line-height: 21px; white-space: nowrap;
  }
  .service-cloud__row--muted { color: var(--grey-word); }
  .service-cloud__row--bright { font-weight: 700; font-size: 16px; }
  .word--lime { color: var(--lime); }
  .word--sky { color: var(--sky); }
  .dot { color: #d8d8d8; }
  .back__stamp {
    position: absolute; right: 32px; top: 18px; width: 72px; height: 46px;
    background: var(--white); color: #111; font-size: 10px; line-height: 1.15;
    display: flex; align-items: center; justify-content: center; text-align: center;
  }
  .back__order {
    position: absolute; left: 30px; bottom: 22px;
    color: var(--lime); font-weight: 800; font-size: 20px;
    transform: rotate(-4.2deg); transform-origin: left bottom;
  }
</style>
</head>
<body>

<section class="postcard front" aria-label="Postcard front">
  <svg class="postcard__art" viewBox="0 0 560 375" aria-hidden="false">
    <defs>
      <linearGradient id="navyShade" x1="0" y1="0" x2="1" y2="1">
        <stop offset="0" stop-color="#243a50"/>
        <stop offset="1" stop-color="#142231"/>
      </linearGradient>
    </defs>
    <rect width="560" height="375" fill="url(#navyShade)"/>
    <polygon points="0,0 110,0 0,130" fill="#2c4560" opacity=".55"/>
    <polygon points="140,0 230,0 60,210 0,210 0,170" fill="#10202f" opacity=".5"/>
    <polygon points="0,290 0,375 70,375" fill="var(--lime)"/>
    <!-- specials band -->
    <path d="M255,0 H560 V142 H228 Q238,60 255,0 Z" fill="var(--lime)"/>
    <!-- dark message area -->
    <path d="M222,156 H560 V375 H150 Q240,300 222,156 Z" fill="var(--ink)"/>
    <rect x="224" y="146" width="336" height="5" fill="var(--sky)"/>
    <polygon points="90,375 230,250 230,262 104,375" fill="var(--sky)"/>
    <!-- showcase circle -->
    <circle cx="118" cy="238" r="112" fill="var(--white)"/>
    <circle cx="118" cy="238" r="104" fill="var(--navy-deep)"/>
    <circle cx="118" cy="238" r="97" fill="var(--white)"/>
    <circle cx="118" cy="238" r="92" fill="var(--photo-blue)" role="img" aria-label="Fan of printed sample brochures, flyers and cards"/>
  </svg>
  <div class="front__logo">YOUR LOGO<br>HERE</div>
  <ul class="front__specials">
    <li>Double your order FREE<br>(order 500 business cards and get 1000)</li>
    <li>250 100lb gloss stock brochures 99.00</li>
    <li>Business packages<br>(cards, envelopes and letterhead) 299</li>
    <li>1000 flyers 140.40</li>
    <li>5000 postcards 179.99</li>
  </ul>
  <p class="front__message">“ Business with no limits, meet mailing with no addresses, Gain new customers through “Open Porch Route Drop”. Reach new customers at their home without needing their address. ”</p>
  <p class="front__contact">Contact Us : order 24/7 orders@inkwillow.com</p>
</section>

<section class="postcard back" aria-label="Postcard back">
  <div class="service-cloud" aria-label="List of print services">
    <div class="service-cloud__row--muted">ners • banners • banners • business cards • business cards • brochures</div>
    <div class="service-cloud__row--bright"><span class="dot">•</span> <span class="word--lime">banners</span> <span class="dot">•</span> <span class="word--sky">booklets</span> <span class="dot">•</span> <span class="word--lime">brochures</span> <span class="dot">•</span> <span class="word--sky">business cards</span></div>
    <div class="service-cloud__row--muted">klets • booklets • booklets • brochures • calendars • catalogs</div>
    <div class="service-cloud__row--bright"><span class="word--lime">calendars</span> <span class="dot">•</span> <span class="word--sky">catalogs</span> <span class="dot">•</span> <span class="word--lime">CD/DVD packages</span> <span class="dot">•</span> <span class="word--sky">envelopes</span></div>
    <div class="service-cloud__row--muted">rochures • business cards • calendars • CD/DVD packages • envelopes</div>
    <div class="service-cloud__row--bright"><span class="word--lime">event tickets</span> <span class="dot">•</span> <span class="word--sky">flyers</span> <span class="dot">•</span> <span class="word--lime">hangtags</span> <span class="dot">•</span> <span class="word--sky">postcards</span> <span class="dot">•</span> <span class="word--lime">posters</span></div>
    <div class="service-cloud__row--muted">endars • catalogs • event tickets • envelopes • hangtags • postcards</div>
    <div class="service-cloud__row--bright"><span class="word--sky">presentation folders</span> <span class="dot">•</span> <span class="word--lime">rack cards</span> <span class="dot">•</span> <span class="word--sky">labels</span> <span class="dot">•</span> <span class="word--lime">table tents</span></div>
    <div class="service-cloud__row--muted">alogs • CD/DVD packages • flyers • posters • rack cards • table tents</div>
    <div class="service-cloud__row--bright"><span class="word--lime">window cling and decal</span> <span class="dot">•</span> <span class="word--sky">banners</span> <span class="dot">•</span> <span class="word--lime">booklets</span> <span class="dot">•</span> <span class="word--sky">brochures</span></div>
    <div class="service-cloud__row--muted">nvelopes • event tickets • hangtags • presentation folders • labels</div>
    <div class="service-cloud__row--muted">yers • hangtags • postcards • posters • rack cards • window cling and decal</div>
    <div class="service-cloud__row--muted">resentation folders • rack cards • labels • table tents • banners</div>
    <div class="service-cloud__row--muted">abels • table tents • window cling and decal • business cards</div>
    <div class="service-cloud__row--muted">indow cling and decal • calendars • catalogs • envelopes</div>
  </div>
  <svg class="postcard__art" viewBox="0 0 560 375">
    <circle cx="408" cy="112" r="46" fill="var(--white)"/>
    <circle cx="408" cy="112" r="41" fill="var(--sky)"/>
    <circle cx="408" cy="112" r="34" fill="#cfe3e8" role="img" aria-label="Printed brochure and folder sample"/>
    <circle cx="506" cy="172" r="42" fill="var(--white)"/>
    <circle cx="506" cy="172" r="37" fill="var(--sky)"/>
    <circle cx="506" cy="172" r="31" fill="#f2f2ee" role="img" aria-label="Yellow booklet sample"/>
    <circle cx="428" cy="214" r="36" fill="var(--white)"/>
    <circle cx="428" cy="214" r="32" fill="var(--lime)"/>
    <circle cx="428" cy="214" r="26" fill="#3d6f9c" role="img" aria-label="Stack of printed flyers"/>
    <!-- footer band -->
    <polygon points="0,322 560,284 560,375 0,375" fill="var(--navy)"/>
    <polygon points="0,312 560,274 560,280 0,318" fill="var(--lime)"/>
    <polygon points="0,319 560,281 560,286 0,324" fill="var(--sky)"/>
  </svg>
  <div class="back__stamp">Postage<br>Stamp</div>
  <p class="back__order">order 24/7 orders@inkwillow.com</p>
</section>

</body>
</html>
```